Verodex business card

Business card for sustainable investment company called "Verodex". Verodex is an exchange platform selling carbon credits between buyers and sellers. Carbon Credits are an environmental commodity for reducing global carbon emissions.

the card should obviously have our logo and the theme should be sustainability/environment mixed with a trading platform.

Contact Information for Business Card

Logo, Name, Title, Phone, Email

Colors
0054AA
0677BA
7BADD7
CADEEF
E8F1F8
0094D4
00A9DD
6FCCEA
C7EBF8
E9F6FB
00AB8E
00BBA5
67D7C9
C6EFE9
E9F9F6
59FF00
82FF00
B8FF75
E3FFCB
F4FFEA

```html
<!DOCTYPE html>
<html lang="en">
<head>
<meta charset="utf-8">
<title>Verodex business card</title>
<link rel="stylesheet" href="https://fonts.googleapis.com/css2?family=Outfit:wght@400;600;700&display=swap">
<style>
  :root {
    --page: #e7e7e7;
    --navy: #1e2e4a;
    --navy-deep: #16243b;
    --navy-light: #2e4660;
    --paper: #f2f2f2;
    --paper-edge: #e6e6e6;
    --brand-blue: #3a86c8;
    --brand-teal: #4bb0c9;
    --ink-light: #f1f3f6;
  }
  * { margin: 0; padding: 0; box-sizing: border-box; }
  html, body {
    width: 1200px; height: 1200px; overflow: hidden;
    background: var(--page);
    font-family: "Outfit", sans-serif;
  }
  .card {
    position: absolute;
    left: 234px;
    width: 731px;
    height: 417px;
    overflow: hidden;
  }
  .card--front {
    top: 160px;
    background: linear-gradient(35deg, var(--navy-deep) 0%, var(--navy) 45%, var(--navy-light) 100%);
  }
  .card--back {
    top: 632px;
    background: linear-gradient(120deg, #f4f4f4 0%, var(--paper-edge) 100%);
  }
  .brand {
    position: absolute;
    display: flex;
    align-items: center;
  }
  .brand__dot {
    border-radius: 50%;
    background: var(--brand-blue);
  }
  .brand__name {
    font-weight: 600;
    letter-spacing: 0.01em;
    line-height: 1;
  }
  .card--front .brand {
    left: 0; right: 0; top: 0; bottom: 0;
    justify-content: center;
    gap: 22px;
  }
  .card--front .brand__dot { width: 58px; height: 58px; }
  .card--front .brand__name { font-size: 62px; color: #f5f6f8; }

  .card--back .brand {
    right: 54px; top: 52px;
    gap: 14px;
  }
  .card--back .brand__dot { width: 34px; height: 34px; }
  .card--back .brand__name { font-size: 32px; color: var(--navy); }

  .wave { position: absolute; inset: 0; width: 100%; height: 100%; }

  .person {
    position: absolute;
    left: 58px; top: 46px;
  }
  .person__name {
    font-size: 34px; font-weight: 700;
    color: var(--brand-blue);
    line-height: 1.1;
  }
  .person__title {
    font-size: 20px; font-weight: 400;
    color: var(--navy);
    margin-top: 6px;
  }
  .contact {
    position: absolute;
    left: 58px; top: 230px;
    list-style: none;
    color: var(--ink-light);
    font-size: 20px;
  }
  .contact__item {
    display: flex; align-items: center; gap: 8px;
    height: 28px;
  }
  .contact__icon { width: 16px; height: 16px; fill: var(--ink-light); }
  .office { position: absolute; left: 58px; top: 319px; color: var(--ink-light); }
  .office__label { font-size: 20px; font-weight: 700; line-height: 28px; }
  .office__address { font-size: 20px; font-weight: 400; line-height: 28px; }
</style>
</head>
<body>
  <section class="card card--front" aria-label="Card front">
    <div class="brand">
      <span class="brand__dot"></span>
      <span class="brand__name">VERODEX</span>
    </div>
  </section>

  <section class="card card--back" aria-label="Card back">
    <svg class="wave" viewBox="0 0 1176 672" preserveAspectRatio="none" aria-hidden="true">
      <path d="M0,313 C170,250 420,250 640,445 C790,575 1020,610 1176,343 L1176,672 L0,672 Z" fill="#1f2f4b"/>
      <path d="M640,445 C790,575 1020,610 1176,343 L1176,540 C1020,680 790,620 640,445 Z" fill="#16243b"/>
    </svg>

    <div class="person">
      <div class="person__name">Mark Halden</div>
      <div class="person__title">Sales Representative</div>
    </div>

    <div class="brand">
      <span class="brand__dot"></span>
      <span class="brand__name">VERODEX</span>
    </div>

    <ul class="contact">
      <li class="contact__item">
        <svg class="contact__icon" viewBox="0 0 24 24" aria-hidden="true"><path d="M6.6 10.8a15.1 15.1 0 0 0 6.6 6.6l2.2-2.2a1 1 0 0 1 1-.25 11.4 11.4 0 0 0 3.6.57 1 1 0 0 1 1 1V20a1 1 0 0 1-1 1A17 17 0 0 1 3 4a1 1 0 0 1 1-1h3.5a1 1 0 0 1 1 1c0 1.25.2 2.45.57 3.6a1 1 0 0 1-.25 1z"/></svg>
        <span>+36 30 555 0142</span>
      </li>
      <li class="contact__item">
        <svg class="contact__icon" viewBox="0 0 24 24" aria-hidden="true"><path d="M2 5h20v14H2z M4 7v.5l8 5 8-5V7l-8 5z" fill-rule="evenodd"/></svg>
        <span>szerviz@verodex.com</span>
      </li>
      <li class="contact__item">
        <svg class="contact__icon" viewBox="0 0 24 24" aria-hidden="true"><path d="M12 2a10 10 0 1 0 0 20 10 10 0 0 0 0-20zm6.9 6h-3a15.7 15.7 0 0 0-1.3-3.6A8 8 0 0 1 18.9 8zM12 4c.8 1.2 1.5 2.5 1.9 4h-3.8c.4-1.5 1.1-2.8 1.9-4zM4.3 14a8 8 0 0 1 0-4h3.4a16 16 0 0 0 0 4zm.8 2h3a15.7 15.7 0 0 0 1.3 3.6A8 8 0 0 1 5.1 16zm3-8h-3a8 8 0 0 1 4.3-3.6C8.8 5.5 8.4 6.7 8.1 8zM12 20c-.8-1.2-1.5-2.5-1.9-4h3.8c-.4 1.5-1.1 2.8-1.9 4zm2.3-6H9.7a14.6 14.6 0 0 1 0-4h4.6a14.6 14.6 0 0 1 0 4zm.3 5.6c.6-1.1 1-2.3 1.3-3.6h3a8 8 0 0 1-4.3 3.6zm1.7-5.6a16 16 0 0 0 0-4h3.4a8 8 0 0 1 0 4z"/></svg>
        <span>www.verodex.com</span>
      </li>
    </ul>

    <div class="office">
      <div class="office__label">Verodex Head Office</div>
      <div class="office__address">Budapest XI. Fenyves utca 12.</div>
    </div>
  </section>
</body>
</html>
```